We are a local Communty Pharmacy wishing to promote and market a specialised Pharmaceutical Service

We would like a design that is professional and enticing ( according to the brief In attached files)
We wish to Market Compounding Pharmacy as a specialist side of our business.
We have the expertise a purpose built preparation laboratory.
The main purpose is an Internet presence that entices prospective patients to contact or visit our physical store.

Target Market(s)

Patients Medicos and Veterinary clients

Industry/Entity Type

Pharmacy

Coding

Coded - Design and coding required

Number of Pages Required

1 page

Requirements
Must have
• Clear friendly image
Nice to have
• soft enticing feel
Should not have
• No crass loud unprofessional elements

```html
<!DOCTYPE html>
<html lang="en">
<head>
<meta charset="utf-8">
<title>Vellmont Compounding Pharmacy</title>
<link href="https://fonts.googleapis.com/css2?family=Open+Sans:wght@400;600;700;800&display=swap" rel="stylesheet">
<style>
:root{
  --blue:#1b65b0;
  --blue-dark:#134d8a;
  --blue-light:#2f86d2;
  --orange:#f3a21b;
  --gold:#e2a920;
  --ink:#3c3c3c;
  --muted:#6b6b6b;
  --line:#e3e6ea;
  --page:#ffffff;
  --soft:#f4f6f8;
}
*{box-sizing:border-box;margin:0;padding:0}
html,body{width:773px;height:1200px;overflow:hidden}
body{font-family:"Open Sans",sans-serif;color:var(--ink);background:var(--page);position:relative}
.wrap{width:670px;margin:0 auto;position:relative}

.site-header{height:77px}
.site-header .wrap{height:77px;display:flex;justify-content:space-between;align-items:center}
.brand{display:flex;align-items:center;gap:10px}
.brand-mark{width:34px;height:34px;background:var(--blue)}
.brand-name{font-weight:800;font-size:22px;color:var(--blue);letter-spacing:.5px}
.header-contact{font-size:9px;color:var(--muted);line-height:1.45}
.header-contact h4{font-size:10px;color:var(--ink);font-weight:700;margin-bottom:3px}
.header-contact .row{display:flex;gap:20px}
.header-contact .col span{display:flex;align-items:center;gap:5px}
.header-contact svg{flex:none}

.main-nav{height:44px;background:linear-gradient(#2a7ccb,var(--blue-dark))}
.main-nav ul{list-style:none;display:flex;height:44px;width:670px;margin:0 auto}
.main-nav li{flex:1;text-align:center;line-height:44px;font-size:10px;font-weight:700;color:#fff;letter-spacing:.5px}
.main-nav li.active{background:var(--orange)}

.hero{height:304px;position:relative;overflow:hidden}
.hero-photo{position:absolute;inset:0;background:linear-gradient(100deg,#cfd9e2 0%,#eef3f7 35%,#d7e6f2 60%,#9ec3e2 100%)}
.hero-copy{position:absolute;left:360px;top:88px}
.hero-copy h1{font-size:31px;font-weight:800;color:var(--blue-dark);letter-spacing:.3px}
.hero-copy .tagline{display:inline-block;margin-top:6px;background:rgba(27,101,176,.85);color:#fff;font-size:13px;font-weight:700;padding:5px 10px}
.btn{display:inline-block;background:var(--orange);color:#fff;font-size:9px;font-weight:700;padding:7px 14px;letter-spacing:.4px}
.hero-copy .btn{margin-top:16px}
.hero-arrow{position:absolute;top:136px;width:24px;height:24px;border-radius:50%;background:rgba(60,60,60,.55)}
.hero-arrow.prev{left:18px}.hero-arrow.next{right:18px}

.intro{padding-top:26px;height:231px}
.intro .wrap{display:flex;gap:22px}
.intro-text{flex:1}
.section-title{font-size:15px;font-weight:800;color:var(--ink);padding-bottom:8px;border-bottom:1px solid var(--line);margin-bottom:10px}
.intro-text p{font-size:9px;line-height:1.6;color:var(--muted);margin-bottom:8px}
.intro-text .btn{margin-top:6px}
.intro-photo{width:170px;height:178px;background:linear-gradient(135deg,#e8eef3,#b9cfe2 60%,#dfe7ee)}

.features{height:266px}
.features-title{text-align:center;font-size:17px;font-weight:600;color:var(--ink);margin-bottom:12px}
.feature-grid{display:flex;gap:24px}
.feature-card{flex:1}
.feature-photo{height:108px;margin-bottom:8px}
.feature-photo.vet{background:linear-gradient(135deg,#f0e9e0,#c9b9a4)}
.feature-photo.scar{background:linear-gradient(135deg,#eef3f8,#a7c3de)}
.feature-photo.thyroid{background:linear-gradient(135deg,#e7eef4,#b8cddf)}
.feature-card h3{font-size:11px;font-weight:700;color:var(--blue);margin-bottom:4px}
.feature-card p{font-size:8px;line-height:1.55;color:var(--muted)}
.feature-card .more{display:block;margin-top:4px;font-size:8px;font-weight:700;color:var(--orange)}
.pager{display:flex;justify-content:center;gap:6px;margin-top:12px}
.pager span{width:16px;height:16px;border-radius:50%;background:#c6ccd2}

.site-footer{position:absolute;left:0;top:974px;width:773px;height:191px;background:var(--blue)}
.site-footer .wrap{display:flex;gap:26px;padding-top:22px}
.footer-col{flex:1;color:#dbe8f5}
.footer-col h4{display:flex;align-items:center;gap:7px;font-size:13px;font-weight:700;color:#fff;margin-bottom:12px}
.hours{width:100%;font-size:8.5px;border-collapse:collapse}
.hours td{padding:5px 0;border-bottom:1px solid rgba(255,255,255,.18)}
.hours td:last-child{text-align:right}
.map{height:110px;background:linear-gradient(135deg,#e9ecef,#cfd6dc)}
.contact-list{list-style:none;font-size:8.5px;line-height:1.5}
.contact-list li{display:flex;gap:7px;margin-bottom:7px}
.contact-list svg{flex:none;margin-top:1px}

.bottom-bar{position:absolute;left:0;top:1165px;width:773px;height:35px;background:var(--gold)}
.bottom-bar .wrap{display:flex;justify-content:space-between;align-items:center;height:35px}
.bottom-links{font-size:8px;color:#fff}
.bottom-links nav{display:flex;gap:12px;margin-bottom:2px}
.bottom-links small{font-size:7px}
.social{display:flex;gap:5px}
.social span{width:16px;height:16px;background:var(--blue-dark)}
</style>
</head>
<body>

<header class="site-header">
  <div class="wrap">
    <div class="brand">
      <span class="brand-mark"></span>
      <span class="brand-name">VELLMONT</span>
    </div>
    <div class="header-contact">
      <h4>Contact us :</h4>
      <div class="row">
        <div class="col">
          <span><svg width="8" height="10" viewBox="0 0 8 10"><path d="M4 0a4 4 0 0 0-4 4c0 3 4 6 4 6s4-3 4-6a4 4 0 0 0-4-4z" fill="#1b65b0"/></svg>Unit 4, 12 Harlow Street</span>
          <span style="padding-left:13px">Ashvale WA 6100</span>
          <span><svg width="9" height="9" viewBox="0 0 10 10"><path d="M2 0l2 3-1 1a6 6 0 0 0 3 3l1-1 3 2-1 2C4 10 0 6 0 2z" fill="#1b65b0"/></svg>08 9000 1234</span>
        </div>
        <div class="col">
          <span><svg width="9" height="9" viewBox="0 0 10 10"><rect width="10" height="10" fill="#1b65b0"/></svg>08 9000 1235</span>
          <span><svg width="10" height="8" viewBox="0 0 10 8"><rect width="10" height="8" fill="#1b65b0"/><path d="M0 0l5 4 5-4" stroke="#fff" fill="none"/></svg>care@vellmontpharmacy.com.au</span>
        </div>
      </div>
    </div>
  </div>
</header>

<nav class="main-nav">
  <ul>
    <li class="active">HOME</li><li>ABOUT US</li><li>SERVICES</li><li>PRODUCTS</li><li>NEWS</li><li>LINKS</li><li>CONTACTS</li>
  </ul>
</nav>

<section class="hero">
  <div class="hero-photo" role="img" aria-label="Photo of a laboratory microscope with sample slides"></div>
  <div class="hero-copy">
    <h1>COMPOUNDING PHARMACY</h1>
    <div class="tagline">IS CUSTOMISED MEDICATIONS FOR PATIENTS</div><br>
    <span class="btn">GET MORE INFO</span>
  </div>
  <svg class="hero-arrow prev" viewBox="0 0 24 24"><circle cx="12" cy="12" r="12" fill="rgba(60,60,60,.55)"/><path d="M14 7l-5 5 5 5" stroke="#fff" stroke-width="2" fill="none"/></svg>
  <svg class="hero-arrow next" viewBox="0 0 24 24"><circle cx="12" cy="12" r="12" fill="rgba(60,60,60,.55)"/><path d="M10 7l5 5-5 5" stroke="#fff" stroke-width="2" fill="none"/></svg>
</section>

<section class="intro">
  <div class="wrap">
    <div class="intro-text">
      <h2 class="section-title">WHAT IS COMPOUNDING PHARMACY?</h2>
      <p>Compounding is the art of preparing medicines to suit the exact needs of a single patient. Before mass production, almost every prescription was made by hand in the pharmacy, and this skill remains a core part of our daily practice.</p>
      <p>Today our pharmacists work with doctors and vets to create strengths, flavours and dose forms that are not available from a manufacturer, helping patients with allergies, swallowing problems or special dosing needs.</p>
      <p>We are proud of our purpose built preparation laboratory and the training of our team, and we welcome you to visit or call our store.</p>
      <span class="btn">READ MORE</span>
    </div>
    <div class="intro-photo" role="img" aria-label="Photo of pharmacists preparing medicine in a laboratory"></div>
  </div>
</section>

<section class="features">
  <div class="wrap">
    <h2 class="features-title">Feature Items</h2>
    <div class="feature-grid">
      <article class="feature-card">
        <div class="feature-photo vet" role="img" aria-label="Photo of a vet examining a dog"></div>
        <h3>Vet Article</h3>
        <p>Our pharmacists prepare tailored doses and flavours for pets, working with your vet so that treatment is simple and safe for animals.</p>
        <span class="more">READ MORE &gt;</span>
      </article>
      <article class="feature-card">
        <div class="feature-photo scar" role="img" aria-label="Photo of a skin therapy treatment"></div>
        <h3>Scar Therapy</h3>
        <p>Custom creams and gels are made to support healing skin, prepared in our laboratory to the strength your doctor has prescribed.</p>
        <span class="more">READ MORE &gt;</span>
      </article>
      <article class="feature-card">
        <div class="feature-photo thyroid" role="img" aria-label="Photo of a doctor checking a patient's neck"></div>
        <h3>Thyroid Extract</h3>
        <p>We compound thyroid preparations in precise strengths, giving patients and prescribers more choice when standard doses do not fit.</p>
        <span class="more">READ MORE &gt;</span>
      </article>
    </div>
    <div class="pager"><span></span><span></span></div>
  </div>
</section>

<footer class="site-footer">
  <div class="wrap">
    <div class="footer-col">
      <h4><svg width="14" height="14" viewBox="0 0 14 14"><circle cx="7" cy="7" r="6" stroke="#fff" stroke-width="1.5" fill="none"/><path d="M7 3v4h3" stroke="#fff" stroke-width="1.5" fill="none"/></svg>Working Hours</h4>
      <table class="hours">
        <tr><td>Sunday</td><td>8.30 AM TO 6.30 PM</td></tr>
        <tr><td>Monday - Friday</td><td>8.30 AM TO 8.00 PM</td></tr>
        <tr><td>Saturday</td><td>8.30 AM TO 6.30 PM</td></tr>
        <tr><td>Public Holidays</td><td>9.00 AM TO 5.00 PM</td></tr>
      </table>
    </div>
    <div class="footer-col">
      <h4><svg width="11" height="14" viewBox="0 0 8 10"><path d="M4 0a4 4 0 0 0-4 4c0 3 4 6 4 6s4-3 4-6a4 4 0 0 0-4-4z" fill="#fff"/><circle cx="4" cy="4" r="1.4" fill="#1b65b0"/></svg>Location</h4>
      <div class="map" role="img" aria-label="Street map showing the pharmacy location"></div>
    </div>
    <div class="footer-col">
      <h4><svg width="14" height="14" viewBox="0 0 10 10"><path d="M2 0l2 3-1 1a6 6 0 0 0 3 3l1-1 3 2-1 2C4 10 0 6 0 2z" fill="#fff"/></svg>Contact Us</h4>
      <ul class="contact-list">
        <li><svg width="8" height="10" viewBox="0 0 8 10"><path d="M4 0a4 4 0 0 0-4 4c0 3 4 6 4 6s4-3 4-6a4 4 0 0 0-4-4z" fill="#fff"/></svg><span>Unit 4, 12 Harlow Street<br>Ashvale WA 6100<br>Western Australia</span></li>
        <li><svg width="9" height="9" viewBox="0 0 10 10"><path d="M2 0l2 3-1 1a6 6 0 0 0 3 3l1-1 3 2-1 2C4 10 0 6 0 2z" fill="#fff"/></svg>08 9000 1234</li>
        <li><svg width="9" height="9" viewBox="0 0 10 10"><rect width="10" height="10" fill="#fff"/></svg>08 9000 1235</li>
        <li><svg width="10" height="8" viewBox="0 0 10 8"><rect width="10" height="8" fill="#fff"/><path d="M0 0l5 4 5-4" stroke="#1b65b0" fill="none"/></svg>care@vellmontpharmacy.com.au</li>
      </ul>
    </div>
  </div>
</footer>

<div class="bottom-bar">
  <div class="wrap">
    <div class="bottom-links">
      <nav><span>Home</span><span>About Us</span><span>Services</span><span>Products</span><span>News</span><span>Links</span><span>Contacts</span></nav>
      <small>Copyright © Compounding Pharmacy 2014 - All rights reserved</small>
    </div>
    <div class="social"><span></span><span></span><span></span><span></span><span></span></div>
  </div>
</div>

</body>
</html>
```